New Business Cards for Tormin Group

We need a new Business Card to compliment our new logo. We are a vibrant design, manufacture and install business providing recreation areas, public parks and Municipal spaces. We want business cards that are classy, modern and clean.

We have recently changed our logo, and are celebrating our 40th anniversary. We want business cards with a new modern design to reflect our status.

Target Market(s)

Customers

Contact Information for Business Card

We need all the details of our 3 offices as per the business card attached. Please disregard the old logo on the business card, the other three files show our new logo.

Requirements
Must have
• All info as per attached business card but with new logo.
Nice to have

```html
<!DOCTYPE html>
<html lang="en">
<head>
<meta charset="utf-8">
<title>Tormin Group – Business Card</title>
<link rel="stylesheet" href="https://fonts.googleapis.com/css2?family=Lato:wght@400;700&display=swap">
<style>
  :root {
    --backdrop: #8a96a6;
    --paper: #ffffff;
    --charcoal: #414143;
    --red: #e8242f;
    --ink: #3a3a3c;
    --band-text: #ffffff;
  }
  * { margin: 0; padding: 0; box-sizing: border-box; }
  html, body {
    width: 1200px; height: 675px; overflow: hidden;
    background: var(--backdrop);
  }
  .card {
    position: absolute; left: 80px; top: 40px;
    width: 1040px; height: 594px;
    background: var(--paper);
    font-family: "Lato", sans-serif;
    color: var(--ink);
    overflow: hidden;
  }
  .card__bands { position: absolute; left: 0; top: 0; width: 1040px; height: 120px; }
  .band--charcoal { fill: var(--charcoal); }
  .band--red { fill: var(--red); }
  .card__web {
    position: absolute; right: 40px; top: 10px;
    color: var(--band-text); font-size: 21px; letter-spacing: 0.5px;
  }
  .offices { position: absolute; left: 96px; top: 96px; }
  .office { margin-bottom: 24px; }
  .office__title { color: var(--red); font-size: 27px; font-weight: 700; line-height: 1.15; margin-bottom: 4px; }
  .office__line { font-size: 17px; line-height: 1.32; }
  .brand {
    position: absolute; right: 120px; top: 92px;
    display: flex; align-items: center; gap: 14px;
  }
  .brand__dot { width: 54px; height: 54px; border-radius: 50%; background: var(--red); }
  .brand__name { color: var(--charcoal); font-size: 40px; font-weight: 700; letter-spacing: 1px; }
  .person { position: absolute; right: 80px; top: 270px; text-align: right; }
  .person__name { color: var(--red); font-size: 38px; font-weight: 700; line-height: 1.1; }
  .person__role { font-size: 21px; margin-top: 4px; }
  .person__contacts { margin-top: 44px; }
  .contact { display: flex; justify-content: flex-end; align-items: center; gap: 12px; font-size: 23px; line-height: 1.45; }
  .contact__icon { width: 20px; height: 20px; fill: var(--red); }
</style>
</head>
<body>
  <div class="card">
    <svg class="card__bands" viewBox="0 0 1040 120" aria-hidden="true">
      <path class="band--red" d="M0 58 H380 C420 58 440 48 470 40 L470 56 C440 62 420 78 380 78 H0 Z"/>
      <path class="band--charcoal" d="M0 0 H1040 V42 H520 C480 42 460 58 400 58 H0 Z"/>
    </svg>
    <div class="card__web">www.tormingroup.com</div>

    <div class="offices">
      <div class="office">
        <div class="office__title">Head Office</div>
        <div class="office__line">P.O. Box: 31842 Abu Dhabi, U.A.E</div>
        <div class="office__line">Tel No: +971 (0)2 5581702</div>
        <div class="office__line">Fax No: +971(0)2 5581703</div>
        <div class="office__line">Email: sales@tormingroup.com</div>
      </div>
      <div class="office">
        <div class="office__title">Dubai Office</div>
        <div class="office__line">P.O. Box: 418260 Dubai, U.A.E</div>
        <div class="office__line">Tel No: +971 (0)4 736214</div>
        <div class="office__line">Fax No: +971(0)4 736215</div>
        <div class="office__line">Email: sales@tormingroup.com</div>
      </div>
      <div class="office">
        <div class="office__title">Qatar Office</div>
        <div class="office__line">P.O. Box: 20937 Doha, Qatar</div>
        <div class="office__line">Tel No: +974 44518036</div>
        <div class="office__line">Fax No: +974 44518037</div>
        <div class="office__line">Email: sales@tormingroup.com</div>
      </div>
    </div>

    <div class="brand">
      <span class="brand__dot"></span>
      <span class="brand__name">Tormin Group</span>
    </div>

    <div class="person">
      <div class="person__name">Daniel Marsh</div>
      <div class="person__role">Managing Partner</div>
      <div class="person__contacts">
        <div class="contact">
          <span>+971 (0)50 384 7720</span>
          <svg class="contact__icon" viewBox="0 0 24 24" aria-hidden="true"><path d="M6.6 10.8a15.1 15.1 0 0 0 6.6 6.6l2.2-2.2a1 1 0 0 1 1-.25 11.4 11.4 0 0 0 3.6.57 1 1 0 0 1 1 1V20a1 1 0 0 1-1 1A17 17 0 0 1 3 4a1 1 0 0 1 1-1h3.5a1 1 0 0 1 1 1c0 1.25.2 2.45.57 3.57a1 1 0 0 1-.25 1z"/></svg>
        </div>
        <div class="contact">
          <span>daniel@tormingroup.com</span>
          <svg class="contact__icon" viewBox="0 0 24 24" aria-hidden="true"><path d="M2 5h20v14H2z M2 5l10 8 10-8" fill="var(--red)"/><path d="M2 5l10 8 10-8" fill="none" stroke="#fff" stroke-width="1.6"/></svg>
        </div>
      </div>
    </div>
  </div>
</body>
</html>
```